Financial Advisor Resource Firm needs business card design

Need business card design for company in Omaha NE called Meridale Circle. We provide resources to financial advisors....workshop programs, retirement analysis, and insurance planning. I would like to see designs that use grays, greens, black, and white colors. The final design should communicate 'collaboration' and be simple yet attractive to financial planning clients. I will attached our logo and another picture of a puzzle piece coming together. I would like the incorporate the puzzle picture somehow, maybe on the back somehow, with color or just the gray scale....OR, the picture be the front of the card with 'Meridale' definition on it (see upload) and then company logo, employee name, title, address on the back (see ppt uploaded). The following disclosure needs to be included somewhere- Advisory services offered through Stonebrook Assets, LLC.
Updates

I uploaded a svg and ai file of the logo

Target Market(s)

Financial planning clients and financial advisors....so pretty diverse age range of about 40-70.

Industry/Entity Type

Financial Planning

Contact Information for Business Card

Tobias L. Fenwright, MBA
Founder/President
5287 E. Larkin Road
Suite 230
Omaha, NE 68190
Phone- (402) 555-0147
Cell- (402) 555-0183
Fax- (402) 555-0129
email- tobias@meridaleplan.example
web address- www.meridaleplan.example

Colors
1b1b1b
474747
d3d3d3
ffffff
9bcb3c
abd036

Requirements
Must have
• Must include logo provided, must be 2 sided, and must have disclosure...all of these items listed in project description

```html
<!DOCTYPE html>
<html lang="en">
<head>
<meta charset="utf-8">
<title>Meridale Circle – Business Card</title>
<link rel="stylesheet" href="https://fonts.googleapis.com/css2?family=Josefin+Sans:wght@600&family=Merriweather:wght@400;700&family=Roboto:wght@300&display=swap">
<style>
  :root {
    --stage: #929395;
    --ink-black: #1b1b1b;
    --ink-dark: #474747;
    --ink-light: #d3d3d3;
    --paper: #ffffff;
    --green: #9bcb3c;
    --text-grey: #3d3d3d;
  }
  * { margin: 0; padding: 0; box-sizing: border-box; }
  html, body { width: 1003px; height: 1200px; overflow: hidden; }
  body { background: var(--stage); position: relative; font-family: "Roboto", sans-serif; }

  .card {
    position: absolute; left: 49px; width: 897px; height: 514px;
    overflow: hidden; box-shadow: 10px 14px 18px rgba(0,0,0,0.35);
  }
  .card--front { top: 63px; }
  .card--back { top: 597px; background: var(--paper); }

  .photo {
    position: absolute; left: 0; top: 0; width: 100%;
    background:
      radial-gradient(ellipse at 60% 70%, #4a4a4a 0%, #363636 35%, transparent 70%),
      linear-gradient(135deg, #2a2a2a 0%, #343434 45%, #2b2b2b 100%);
  }
  .card--front .photo { height: 100%; }
  .card--back .photo { height: 221px; }

  .brand {
    position: absolute; font-family: "Josefin Sans", sans-serif; font-weight: 600;
    text-transform: uppercase; line-height: 1; text-align: right;
  }
  .brand__main { display: block; letter-spacing: 1px; }
  .brand__sub { display: block; letter-spacing: 3px; }

  .card--front .brand { left: 71px; top: 93px; width: 432px; color: var(--paper); }
  .card--front .brand__main { font-size: 56px; }
  .card--front .brand__sub { font-size: 20px; margin-top: 6px; }

  .website {
    position: absolute; left: 0; right: 0; top: 432px; line-height: 24px; text-align: center;
    color: var(--paper); font-weight: 300; font-size: 20px; letter-spacing: 3.6px;
  }

  .person { position: absolute; left: 68px; top: 84px; font-family: "Merriweather", serif; }
  .person__name { color: var(--green); font-weight: 700; font-size: 20px; letter-spacing: 0.8px; text-transform: uppercase; }
  .person__title { color: var(--paper); font-weight: 400; font-size: 19px; margin-top: 10px; }

  .contacts { position: absolute; left: 68px; top: 250px; list-style: none; }
  .contacts li { display: flex; align-items: center; height: 35.5px; }
  .contacts svg { width: 28px; height: 28px; flex: none; margin-right: 21px; }
  .contacts span { color: var(--text-grey); font-weight: 300; font-size: 22px; }

  .card--back .brand { left: 593px; top: 267px; width: 232px; color: var(--ink-black); }
  .card--back .brand__main { font-size: 30px; }
  .card--back .brand__sub { font-size: 11px; margin-top: 3px; letter-spacing: 2px; }

  .disclosure {
    position: absolute; left: 68px; top: 470px; line-height: 16px;
    color: var(--ink-dark); font-weight: 300; font-size: 12px; letter-spacing: 0.3px;
  }
</style>
</head>
<body>

<section class="card card--front">
  <div class="photo" role="img" aria-label="Greyscale photo of several hands joining puzzle pieces together"></div>
  <div class="brand"><span class="brand__main">Meridale</span><span class="brand__sub">Circle</span></div>
  <p class="website">www.meridaleplan.example</p>
</section>

<section class="card card--back">
  <div class="photo" role="img" aria-label="Greyscale photo of hands joining puzzle pieces together"></div>
  <div class="person">
    <p class="person__name">Tobias L. Fenwright, MBA</p>
    <p class="person__title">Founder/President</p>
  </div>

  <ul class="contacts">
    <li>
      <svg viewBox="0 0 28 28" aria-hidden="true"><circle cx="14" cy="14" r="12.5" fill="none" stroke="#3d3d3d" stroke-width="1.4"/><path d="M9.5 8.5c.8-.8 1.6-.6 2 .1l1 1.8c.3.6.2 1.2-.3 1.6l-.7.6c.6 1.4 1.8 2.6 3.2 3.2l.6-.7c.4-.5 1-.6 1.6-.3l1.8 1c.7.4.9 1.2.1 2-1.4 1.4-3.4 1-6-1.3-2.5-2.4-4.7-5.4-3.3-8z" fill="#3d3d3d"/></svg>
      <span>(402) 555-0147</span>
    </li>
    <li>
      <svg viewBox="0 0 28 28" aria-hidden="true"><circle cx="14" cy="14" r="12.5" fill="none" stroke="#3d3d3d" stroke-width="1.4"/><rect x="10.5" y="7" width="7" height="14" rx="1.2" fill="none" stroke="#3d3d3d" stroke-width="1.4"/><circle cx="14" cy="18.6" r="0.8" fill="#3d3d3d"/></svg>
      <span>(402) 555-0183</span>
    </li>
    <li>
      <svg viewBox="0 0 28 28" aria-hidden="true"><circle cx="14" cy="14" r="12.5" fill="none" stroke="#3d3d3d" stroke-width="1.4"/><rect x="10" y="7.5" width="8" height="4" fill="#3d3d3d"/><rect x="7.5" y="11.5" width="13" height="6" rx="1" fill="#3d3d3d"/><rect x="10" y="15.5" width="8" height="5" fill="#fff" stroke="#3d3d3d" stroke-width="1.2"/></svg>
      <span>(402) 555-0129</span>
    </li>
    <li>
      <svg viewBox="0 0 28 28" aria-hidden="true"><circle cx="14" cy="14" r="12.5" fill="none" stroke="#3d3d3d" stroke-width="1.4"/><rect x="8.5" y="10" width="11" height="8" fill="#3d3d3d"/><path d="M8.5 10l5.5 4.5 5.5-4.5" fill="none" stroke="#fff" stroke-width="1"/></svg>
      <span>tobias@meridaleplan.example</span>
    </li>
    <li>
      <svg viewBox="0 0 28 28" aria-hidden="true"><circle cx="14" cy="14" r="12.5" fill="none" stroke="#3d3d3d" stroke-width="1.4"/><path d="M14 21s-5-5-5-8.5a5 5 0 0 1 10 0C19 16 14 21 14 21z" fill="none" stroke="#3d3d3d" stroke-width="1.4"/><circle cx="14" cy="12.5" r="1.8" fill="#3d3d3d"/></svg>
      <span>5287 E. Larkin Road Suite 230 Omaha, NE 68190</span>
    </li>
  </ul>

  <div class="brand"><span class="brand__main">Meridale</span><span class="brand__sub">Circle</span></div>

  <p class="disclosure">Advisory services offered through Stonebrook Assets, LLC.</p>
</section>

</body>
</html>
```